Suds Haven Laundromat Wordpress Design

We need a Wordpress website design for our laundromat, Suds Haven Atlanta, at www.sudshavenatlanta-example.com. We would like to have 6 pages: Home, About Us, Services, Locations, Reviews and Contact us. We will provide content for the text on each page. What we do: We are a full service laundromat that provides dry cleaning drop off, professional laundry services, wash dry fold and self service laundry to the local community. We would like to use the color scheme from our logo to convey a warm, safe, and bright business that caters to its diverse community.
Updates

I like the structure of this laundromat website: http://www.washtroveusa-example.com/ Using my logo and color scheme in the above referenced website is what. Am looking for. The photos attached to the project with the female model should be used as a primary focus and supplemented by actual photos of the equipment.

Target Market(s)

Our target market is a diverse group of people from Midtown Atlanta - LGBTQ community /Locals/Regulars that have been coming to laundromat for 30 years.

Industry/Entity Type

Laundromat

Coding

Coded - Design and coding required

Number of Pages Required

5+ page

Font styles to use
Sans Serif

Colors
0054AA
0677BA
7BADD7
CADEEF
E8F1F8

Requirements
Must have
• Feature this video on the main page: https://videohost-example.com/xq7Rm2bPz4k

```html
<!DOCTYPE html>
<html lang="en">
<head>
<meta charset="utf-8">
<title>Suds Haven Laundromat</title>
<link href="https://fonts.googleapis.com/css2?family=Barlow:wght@400;500;600;700&family=Open+Sans:wght@400;600&display=swap" rel="stylesheet">
<style>
:root{
  --navy:#0054AA;
  --blue:#0677BA;
  --band:#1f68c6;
  --sky:#7BADD7;
  --pale:#CADEEF;
  --mist:#E8F1F8;
  --ink:#1d1d1d;
  --body:#4a4a4a;
  --footer:#0b1a30;
  --star:#f5a623;
  --white:#ffffff;
}
*{margin:0;padding:0;box-sizing:border-box}
html,body{width:1200px;height:4076px;overflow:hidden}
body{position:relative;background:var(--white);font-family:"Open Sans",sans-serif;color:var(--body)}
.abs{position:absolute}
.heading{font-family:"Barlow",sans-serif}

/* header */
.site-header{left:0;top:0;width:1200px;height:95px;background:var(--white)}
.brand{left:110px;top:22px;display:flex;align-items:center;gap:10px;font-family:"Barlow",sans-serif;font-weight:600;font-size:30px;color:var(--blue)}
.brand-dot{width:14px;height:14px;border-radius:50%;background:var(--sky)}
.nav{right:111px;top:37px;display:flex;gap:17px;font-family:"Barlow",sans-serif;font-size:16px;color:var(--ink);letter-spacing:.2px}

/* hero */
.hero-photo{left:0;top:95px;width:1200px;height:602px;background:linear-gradient(100deg,#4a4f55 0%,#8c9399 35%,#b7bdc2 55%,#9aa2a8 75%,#6f767c 100%)}
.hero-shade{left:0;top:95px;width:700px;height:602px;background:linear-gradient(90deg,rgba(20,24,30,.6),rgba(20,24,30,0))}
.hero-kicker{left:108px;top:206px;font-family:"Barlow",sans-serif;font-size:25px;color:var(--white);display:flex;align-items:center;gap:14px}
.hero-kicker span{display:block;width:68px;height:2px;background:var(--white)}
.hero-title{left:108px;top:262px;font-family:"Barlow",sans-serif;font-weight:600;font-size:50px;line-height:60px;color:var(--white);text-transform:uppercase}
.btn{display:inline-flex;align-items:center;justify-content:center;background:var(--navy);color:var(--white);font-family:"Barlow",sans-serif;font-size:17px;border-radius:28px;box-shadow:0 0 0 3px var(--white),0 0 0 5px var(--navy)}
.hero-btn{left:112px;top:475px;width:167px;height:52px}

/* about */
.about-circle{border-radius:50%;border:5px solid var(--white)}
.c-model{left:108px;top:776px;width:320px;height:320px;background:radial-gradient(circle at 40% 40%,#c58a5a,#2f6bc4 70%,#d7dde2)}
.c-towels{left:405px;top:790px;width:165px;height:165px;background:linear-gradient(140deg,#d9dee1,#f5f5f2,#8b969c)}
.c-machines{left:343px;top:938px;width:240px;height:240px;background:linear-gradient(180deg,#b9d3cf 0%,#9fb9b6 45%,#4d5356 100%)}
.section-ghost{font-family:"Barlow",sans-serif;font-weight:600;color:rgba(0,0,0,.07);white-space:nowrap}
.about-ghost{left:680px;top:800px;font-size:60px}
.about-rule{left:633px;top:845px;width:36px;height:3px;background:var(--navy)}
.about-title{left:680px;top:828px;font-family:"Barlow",sans-serif;font-weight:600;font-size:30px;color:var(--ink)}
.about-text{left:680px;top:876px;width:410px;font-size:17px;line-height:30px}
.about-text p+p{margin-top:9px}
.about-btn{left:682px;top:1082px;width:148px;height:47px}

/* services */
.services-band{left:0;top:1262px;width:1200px;height:830px}
.center-title{left:0;width:1200px;text-align:center;font-family:"Barlow",sans-serif;font-weight:600}
.svc-title{top:1430px;font-size:36px;color:var(--white)}
.svc-ghost{top:1398px;font-size:78px;color:rgba(255,255,255,.13)}
.title-rules{left:395px;width:410px;height:3px;display:flex;justify-content:space-between}
.title-rules i{display:block;width:36px;height:3px}
.card{width:222px;height:391px;top:1543px;background:var(--white);border-radius:111px 111px 4px 4px;text-align:center}
.card-icon{position:absolute;left:51px;top:26px;width:120px;height:120px}
.card-title{position:absolute;left:0;top:166px;width:100%;font-family:"Barlow",sans-serif;font-weight:600;font-size:18px;line-height:31px;color:var(--blue);text-transform:uppercase}
.card-text{position:absolute;left:16px;top:236px;width:190px;font-size:16.5px;line-height:30px}
.card-link{position:absolute;left:0;top:343px;width:100%;font-family:"Barlow",sans-serif;font-weight:500;font-size:17px;color:var(--blue);text-decoration:underline}

/* video */
.video-title{top:2204px;font-size:38px;color:var(--ink)}
.video-ghost{top:2170px;font-size:78px;color:rgba(0,0,0,.06)}
.video-frame{left:116px;top:2322px;width:968px;height:493px;background:#111;box-shadow:0 3px 14px rgba(0,0,0,.25);border-radius:3px;overflow:hidden}
.video-still{left:0;top:16px;width:968px;height:405px;background:linear-gradient(100deg,#3d4a48 0%,#6f7d76 30%,#9aa59c 55%,#6e7a78 80%,#3f4a4c 100%)}
.video-bar{left:0;top:421px;width:968px;height:72px;background:#151515}
.progress{left:16px;top:450px;width:936px;height:4px;background:#555}
.progress i{display:block;width:26px;height:4px;background:#e01}
.video-time{left:145px;top:466px;color:var(--white);font-size:12px;font-family:"Barlow",sans-serif}

/* testimonials */
.testi-band{left:0;top:2900px;width:1200px;height:800px}
.testi-title{top:3097px;font-size:38px;color:var(--white)}
.testi-ghost{top:3060px;font-size:80px;color:rgba(255,255,255,.13)}
.quote{top:3224px;width:303px;height:319px;background:var(--white);border-radius:8px;text-align:center}
.quote:after{content:"";position:absolute;left:34px;bottom:-22px;border-left:22px solid var(--white);border-bottom:22px solid transparent}
.stars{position:absolute;left:0;top:46px;width:100%;display:flex;justify-content:center;gap:4px}
.quote p{position:absolute;left:26px;top:104px;width:251px;font-size:17px;line-height:30px}
.reviewer{top:3568px;width:303px;text-align:center;font-family:"Open Sans",sans-serif;font-weight:600;font-size:17px;color:var(--white)}

/* footer */
.site-footer{left:0;top:3688px;width:1200px;height:388px;background:var(--footer)}
.footer-brand{left:0;top:3782px;width:1200px;display:flex;justify-content:center;align-items:center;gap:10px;font-family:"Barlow",sans-serif;font-weight:600;font-size:28px;color:var(--white)}
.footer-nav{top:3892px;font-family:"Barlow",sans-serif;font-size:17px;line-height:30px;color:var(--white);text-transform:uppercase}
.footer-divider{top:3888px;width:1px;height:88px;background:rgba(255,255,255,.3)}
.footer-info{top:3888px;font-family:"Barlow",sans-serif;font-size:14.5px;line-height:30px;color:var(--white);text-transform:uppercase}
.footer-email{text-transform:none}
.footer-rule{left:116px;top:4006px;width:968px;height:1px;background:rgba(255,255,255,.25)}
.copyright{left:0;top:4030px;width:1200px;text-align:center;font-family:"Barlow",sans-serif;font-size:15px;color:var(--white)}
</style>
</head>
<body>

<header class="abs site-header">
  <div class="abs brand"><span class="brand-dot"></span>Suds Haven</div>
  <nav class="abs nav"><span>HOME</span><span>ABOUT US</span><span>SERVICES</span><span>LOCATIONS</span><span>REVIEWS</span><span>CONTACT US</span></nav>
</header>

<section>
  <div class="abs hero-photo" role="img" aria-label="Woman in a blue dress walking past a row of front-load washing machines"></div>
  <div class="abs hero-shade"></div>
  <div class="abs hero-kicker">BEST COIN LAUNDRY<span></span></div>
  <h1 class="abs hero-title">One of Atlanta's First,<br>Finest, &amp; Friendliest<br>Coin Laundries</h1>
  <a class="abs btn hero-btn">LEARN MORE</a>
  <svg class="abs" style="left:0;top:600px" width="1200" height="100" viewBox="0 0 1200 100" preserveAspectRatio="none">
    <path d="M0 30 C150 10 240 65 380 72 C560 82 800 40 980 20 C1080 8 1150 14 1200 22 L1200 100 L0 100 Z" fill="#ffffff"/>
    <path d="M0 30 C150 10 240 65 380 72" stroke="#0677BA" stroke-width="5" fill="none"/>
    <path d="M1020 20 C1100 6 1160 8 1200 16" stroke="#0677BA" stroke-width="5" fill="none"/>
  </svg>
</section>

<section>
  <div class="abs about-circle c-model" role="img" aria-label="Woman with red hair in a blue dress beside washing machines"></div>
  <div class="abs about-circle c-towels" role="img" aria-label="Stack of folded white towels"></div>
  <div class="abs about-circle c-machines" role="img" aria-label="Laundromat wall with a row of washers"></div>
  <div class="abs section-ghost about-ghost">About Us</div>
  <div class="abs about-rule"></div>
  <h2 class="abs about-title">About Us</h2>
  <div class="abs about-text">
    <p>Lorem ipsum dolor sit amet, consectetur adipiscing elit. Cras nec blandit neque, vel feugiat est. Sudisse odio tortor, venenatis in diam sit amet.</p>
    <p>Lorem ipsum dolor sit amet, consectetur adipiscing elit. Cras nec blandit neque, vel feugiat est. Sudisse odio tortor, venenatis in diam sit amet.</p>
  </div>
  <a class="abs btn about-btn">LEARN MORE</a>
</section>

<section>
  <svg class="abs services-band" viewBox="0 0 1200 830" preserveAspectRatio="none">
    <defs><linearGradient id="bandFill" x1="0" y1="0" x2="1" y2="1"><stop offset="0" stop-color="#1d63bf"/><stop offset="1" stop-color="#2a72cf"/></linearGradient></defs>
    <path d="M0 10 C200 100 420 70 620 40 C820 10 1000 0 1200 50 L1200 800 C1000 750 820 745 620 760 C400 780 200 830 0 780 Z" fill="#CADEEF"/>
    <path d="M0 22 C200 110 420 80 620 50 C820 22 1000 14 1200 66 L1200 788 C1000 740 820 735 620 748 C400 766 200 816 0 770 Z" fill="url(#bandFill)"/>
  </svg>
  <div class="abs center-title svc-ghost">Services</div>
  <div class="abs title-rules" style="top:1450px"><i style="background:#5c93d8"></i><i style="background:#5c93d8"></i></div>
  <h2 class="abs center-title svc-title">Services</h2>

  <div class="abs card" style="left:111px">
    <svg class="card-icon" viewBox="0 0 120 120"><circle cx="60" cy="60" r="56" fill="none" stroke="#0677BA" stroke-width="4"/><circle cx="62" cy="62" r="46" fill="#7BADD7"/><rect x="46" y="40" width="32" height="44" rx="6" fill="none" stroke="#0054AA" stroke-width="3"/><path d="M62 30 v10 M52 40 l10 14 10-14" stroke="#0054AA" stroke-width="3" fill="none"/></svg>
    <div class="card-title">Dry Cleaning<br>Drop Off</div>
    <div class="card-text">Mauris fermentum diam lectus, et ultr ices orci congue at.</div>
    <a class="card-link">READ MORE</a>
  </div>
  <div class="abs card" style="left:362px">
    <svg class="card-icon" viewBox="0 0 120 120"><circle cx="60" cy="60" r="56" fill="none" stroke="#0677BA" stroke-width="4"/><circle cx="62" cy="62" r="46" fill="#7BADD7"/><rect x="40" y="40" width="40" height="44" rx="5" fill="none" stroke="#0054AA" stroke-width="3"/><circle cx="60" cy="66" r="11" fill="none" stroke="#0054AA" stroke-width="3"/><path d="M40 50 h40" stroke="#0054AA" stroke-width="3"/></svg>
    <div class="card-title">Professional<br>Laundry</div>
    <div class="card-text">Mauris fermentum diam lectus, et ultr ices orci congue at.</div>
    <a class="card-link">READ MORE</a>
  </div>
  <div class="abs card" style="left:614px">
    <svg class="card-icon" viewBox="0 0 120 120"><circle cx="60" cy="60" r="56" fill="none" stroke="#0677BA" stroke-width="4"/><circle cx="62" cy="62" r="46" fill="#7BADD7"/><path d="M42 46 h36 M42 56 h36 M42 66 h36 M42 76 h36" stroke="#0054AA" stroke-width="4" stroke-linecap="round"/></svg>
    <div class="card-title">Wash Dry Fold</div>
    <div class="card-text" style="top:205px">Mauris fermentum diam lectus, et ultr ices orci congue at.</div>
    <a class="card-link">READ MORE</a>
  </div>
  <div class="abs card" style="left:866px">
    <svg class="card-icon" viewBox="0 0 120 120"><circle cx="60" cy="60" r="56" fill="none" stroke="#0677BA" stroke-width="4"/><circle cx="62" cy="62" r="46" fill="#7BADD7"/><path d="M44 44 l18 36 h18 l-4-20 z" fill="none" stroke="#0054AA" stroke-width="3" stroke-linejoin="round"/><path d="M72 38 l3 6 6 1-6 3-3 6-3-6-6-3 6-1z" fill="#0054AA"/></svg>
    <div class="card-title">Self Service<br>Laundry</div>
    <div class="card-text">Mauris fermentum diam lectus, et ultr ices orci congue at.</div>
    <a class="card-link">READ MORE</a>
  </div>
</section>

<section>
  <div class="abs center-title video-ghost">Our Video</div>
  <div class="abs title-rules" style="top:2228px;left:380px;width:440px"><i style="background:#0054AA"></i><i style="background:#0054AA"></i></div>
  <h2 class="abs center-title video-title">Our Video</h2>
  <div class="abs video-frame">
    <div class="abs video-still" role="img" aria-label="Video still of a customer carrying a laundry basket inside the laundromat"></div>
    <div class="abs video-bar"></div>
    <div class="abs progress"><i></i></div>
    <svg class="abs" style="left:30px;top:462px" width="100" height="20" viewBox="0 0 100 20"><path d="M2 3 l12 7 -12 7z" fill="#fff"/><path d="M44 4 l9 6 -9 6z M55 4 v12" fill="#fff" stroke="#fff" stroke-width="2"/><path d="M84 7 h4 l5-4 v14 l-5-4 h-4z" fill="#fff"/></svg>
    <div class="abs video-time">0:07 / 4:33</div>
    <svg class="abs" style="left:800px;top:462px" width="150" height="20" viewBox="0 0 150 20"><rect x="0" y="6" width="22" height="8" rx="4" fill="#888"/><circle cx="17" cy="10" r="5" fill="#fff"/><rect x="46" y="3" width="18" height="14" rx="2" fill="#fff"/><circle cx="90" cy="10" r="6" fill="#fff"/><path d="M120 4 h-5 v5 M130 4 h5 v5 M120 16 h-5 v-5 M130 16 h5 v-5" stroke="#fff" stroke-width="2" fill="none"/></svg>
  </div>
</section>

<section>
  <svg class="abs testi-band" viewBox="0 0 1200 800" preserveAspectRatio="none" role="img" aria-label="Blue background with soft bubbles of laundry">
    <defs><linearGradient id="testiFill" x1="0" y1="0" x2="0" y2="1"><stop offset="0" stop-color="#1c62bf"/><stop offset="1" stop-color="#2e78cf"/></linearGradient></defs>
    <path d="M0 40 C220 -10 380 60 560 70 C760 80 1000 10 1200 0 L1200 800 L0 800 Z" fill="url(#testiFill)"/>
    <circle cx="250" cy="200" r="80" fill="#ffffff" opacity=".07"/>
    <circle cx="80" cy="300" r="50" fill="#ffffff" opacity=".06"/>
    <circle cx="1050" cy="190" r="90" fill="#ffffff" opacity=".07"/>
    <circle cx="560" cy="480" r="70" fill="#ffffff" opacity=".05"/>
  </svg>
  <div class="abs center-title testi-ghost">Testimonials</div>
  <h2 class="abs center-title testi-title">Testimonials</h2>

  <div class="abs quote" style="left:109px">
    <svg class="stars" viewBox="0 0 120 20" height="20"><g fill="#f5a623"><path id="st" d="M10 1 l2.6 6 6.4.5-4.9 4.2 1.5 6.3L10 14.6 4.4 18l1.5-6.3L1 7.5l6.4-.5z"/><use href="#st" x="24"/><use href="#st" x="48"/><use href="#st" x="72"/><use href="#st" x="96"/></g></svg>
    <p>“Ut a ipsum feugiat, luctus diam dictum, vehicula sapien. Suspendisse sagittis, ex id ultricies suscipit, neque leo ornare diam, et tristique justo elit vel tellus.”</p>
  </div>
  <div class="abs quote" style="left:448px">
    <svg class="stars" viewBox="0 0 120 20" height="20"><g fill="#f5a623"><use href="#st"/><use href="#st" x="24"/><use href="#st" x="48"/><use href="#st" x="72"/><use href="#st" x="96"/></g></svg>
    <p>“Ut a ipsum feugiat, luctus diam dictum, vehicula sapien. Suspendisse sagittis, ex id ultricies suscipit, neque leo ornare diam, et tristique justo elit vel tellus.”</p>
  </div>
  <div class="abs quote" style="left:785px">
    <svg class="stars" viewBox="0 0 120 20" height="20"><g fill="#f5a623"><use href="#st"/><use href="#st" x="24"/><use href="#st" x="48"/><use href="#st" x="72"/><use href="#st" x="96"/></g></svg>
    <p>“Ut a ipsum feugiat, luctus diam dictum, vehicula sapien. Suspendisse sagittis, ex id ultricies suscipit, neque leo ornare diam, et tristique justo elit vel tellus.”</p>
  </div>
  <div class="abs reviewer" style="left:109px">Dana Morrow, Atlanta</div>
  <div class="abs reviewer" style="left:448px">Dana Morrow, Atlanta</div>
  <div class="abs reviewer" style="left:785px">Dana Morrow, Atlanta</div>
</section>

<footer>
  <div class="abs site-footer"></div>
  <svg class="abs" style="left:0;top:3640px" width="1200" height="80" viewBox="0 0 1200 80" preserveAspectRatio="none">
    <path d="M0 40 C200 20 300 60 520 55 C760 50 960 10 1200 30 L1200 80 L0 80 Z" fill="#0b1a30"/>
    <path d="M0 40 C200 20 300 60 520 55" stroke="#0677BA" stroke-width="5" fill="none"/>
    <path d="M820 28 C960 12 1080 16 1200 30" stroke="#0677BA" stroke-width="5" fill="none"/>
  </svg>
  <div class="abs footer-brand"><span class="brand-dot"></span>Suds Haven</div>
  <div class="abs footer-nav" style="left:110px">Home<br>About Us<br>Services</div>
  <div class="abs footer-nav" style="left:238px">Locations<br>Reviews<br>Contact Us</div>
  <div class="abs footer-divider" style="left:361px"></div>
  <svg class="abs" style="left:387px;top:3894px" width="18" height="26" viewBox="0 0 18 26"><path d="M9 1 C4 1 1 5 1 9 C1 15 9 25 9 25 C9 25 17 15 17 9 C17 5 14 1 9 1Z" fill="#0677BA"/><circle cx="9" cy="9" r="3.5" fill="#0b1a30"/></svg>
  <div class="abs footer-info" style="left:425px">Linden Court Shopping Center,<br>820 Maple Row NE., # 12,<br>Atlanta, GA 30300</div>
  <div class="abs footer-divider" style="left:681px"></div>
  <svg class="abs" style="left:702px;top:3896px" width="22" height="22" viewBox="0 0 24 24"><path d="M6.6 10.8c1.4 2.8 3.8 5.1 6.6 6.6l2.2-2.2c.3-.3.7-.4 1-.2 1.1.4 2.3.6 3.6.6.6 0 1 .4 1 1V20c0 .6-.4 1-1 1C10.6 21 3 13.4 3 4c0-.6.4-1 1-1h3.5c.6 0 1 .4 1 1 0 1.3.2 2.5.6 3.6.1.3 0 .7-.2 1z" fill="#0677BA"/></svg>
  <div class="abs footer-info" style="left:742px">(404) 555-0142<br>Call Us Now</div>
  <div class="abs footer-divider" style="left:868px"></div>
  <svg class="abs" style="left:893px;top:3897px" width="28" height="20" viewBox="0 0 28 20"><rect x="0" y="0" width="28" height="20" rx="2" fill="#0677BA"/><path d="M2 3 l12 9 12-9" stroke="#0b1a30" stroke-width="2" fill="none"/></svg>
  <div class="abs footer-info" style="left:937px"><span class="footer-email">hello@sudshaven-example.com</span><br>Mail Us</div>
  <div class="abs footer-rule"></div>
  <div class="abs copyright">2021 Suds Haven. All Rights Reserved.</div>
</footer>

</body>
</html>
```